Meridale Real Estate

We are looking for help with web design for a new company that is revolutionizing the real estate world on the listing side: by charing per hour for top level professional real estate services. We would like the concept to be simple, clean and easily understood.
Updates

We want this website to actually function, not just a static design.

Industry/Entity Type

Real Estate

```html
<!DOCTYPE html>
<html lang="en">
<head>
<meta charset="utf-8">
<title>Meridale Real Estate</title>
<link rel="stylesheet" href="https://fonts.googleapis.com/css2?family=Arimo:wght@400;700&display=swap">
<style>
:root{
  --ink:#03030a;
  --accent:#2eaee3;
  --accent-soft:#7fd3f3;
  --text:#555;
  --muted:#8a8a8a;
  --heading:#444;
  --panel:#ffffff;
  --band:#e6e6e6;
  --line:#d8d8d8;
}
*{box-sizing:border-box;margin:0;padding:0}
html,body{width:1200px;height:1192px;overflow:hidden}
body{position:relative;font-family:"Arimo",Arial,sans-serif;background:#fff;color:var(--text);font-size:9px}
a{color:inherit;text-decoration:none}

/* header */
.site-header{position:absolute;left:0;top:0;width:1200px;height:190px;background:var(--ink)}
.brand{position:absolute;left:213px;top:44px;display:flex;align-items:center;gap:12px}
.brand-dot{width:34px;height:34px;border:2px solid var(--accent);border-radius:50%}
.brand-name{color:var(--accent);font-size:19px;letter-spacing:4px;text-transform:uppercase;font-weight:400;line-height:1.3;width:170px}
.follow{position:absolute;left:783px;top:59px;width:180px;text-align:right;color:#9a9a9a;font-size:8px;white-space:nowrap}
.follow b{color:#fff}
.search-box{position:absolute;left:853px;top:79px;width:110px;height:25px;border:1px solid #555;background:#050508}
.search-box svg{position:absolute;left:8px;top:8px}
.main-nav{position:absolute;left:200px;top:155px;width:760px;height:35px;background:linear-gradient(90deg,#0a0a0a 0%,#3a3a3a 30%,#4a4a4a 60%,#2a2a2a 85%,#0a0a0a 100%)}
.main-nav a{position:absolute;top:0;height:35px;line-height:35px;color:#e8e8e8;font-size:9px}
.main-nav a.active{color:var(--accent);font-weight:700;border-top:3px solid var(--accent);line-height:31px;padding:0 10px}

/* hero */
.hero{position:absolute;left:0;top:190px;width:1200px;height:234px;background:linear-gradient(180deg,#9fb0bf 0%,#e9e9e6 35%,#d9d4ca 70%,#6f6a5c 100%)}
.listing{position:absolute;left:760px;top:213px;width:203px;height:191px;background:rgba(20,20,24,.9);border-top:4px solid var(--accent);color:#ddd;padding:10px 16px}
.listing-title{font-size:11px;font-weight:400;color:#fff;line-height:14px;margin-bottom:8px}
.listing dl{display:grid;grid-template-columns:1fr auto;font-size:7px}
.listing dt,.listing dd{height:15px;line-height:15px;border-bottom:1px solid #2d2d33}
.listing dd{text-align:right}
.listing .more{display:block;margin-top:6px;color:var(--accent);font-size:7px;text-decoration:underline;font-weight:700}

/* search & welcome */
.band{position:absolute;left:0;top:424px;width:1200px;height:446px;background:var(--band)}
.finder{position:absolute;left:197px;top:441px;width:766px;height:175px;background:var(--panel);border-top:4px solid var(--accent)}
.panel-title{font-size:11px;font-weight:400;color:var(--heading);text-transform:uppercase;line-height:13px}
.finder-title{position:absolute;left:20px;top:24px}
.field{position:absolute;font-size:7px;color:#444}
.field span{display:block;margin-bottom:5px}
.field i{display:block;width:98px;height:21px;border:1px solid #ccc;background:#fafafa;position:relative}
.field i.sel::after{content:"";position:absolute;right:7px;top:8px;border:4px solid transparent;border-top-color:#999}
.btn-search{position:absolute;left:18px;top:136px;width:52px;height:20px;background:var(--accent);color:#fff;font-size:8px;text-align:center;line-height:20px}
.hint{position:absolute;left:90px;top:142px;font-size:7px;color:#666}
.hint a{color:var(--accent);text-decoration:underline;margin-left:4px}
.divider{position:absolute;left:372px;top:22px;width:1px;height:130px;background:var(--line)}
.welcome{position:absolute;left:417px;top:24px;width:300px}
.welcome-lead{color:var(--accent);font-size:8px;line-height:14px;margin-top:12px;text-transform:uppercase;width:240px}
.welcome-text{font-size:7px;line-height:13px;color:var(--muted);margin-top:10px}
.btn-alert{display:inline-block;margin-top:12px;background:#4a4a4a;color:#fff;font-size:8px;padding:6px 12px}

.section-title{position:absolute;left:0;top:645px;width:1200px;text-align:center;font-size:11px;font-weight:400;color:var(--heading);text-transform:uppercase}
.offer{position:absolute;top:675px;width:143px}
.offer .thumb{width:143px;height:105px;background:#fff;padding:4px;box-shadow:0 0 2px rgba(0,0,0,.15);position:relative}
.offer .thumb div{width:100%;height:100%}
.offer .date{position:absolute;left:8px;bottom:8px;width:34px;height:26px;background:rgba(20,20,20,.85);color:#fff;text-align:center;font-size:10px;font-weight:700;line-height:12px;padding-top:2px}
.offer .date small{display:block;font-size:7px;font-weight:400}
.offer h4{font-size:8px;font-weight:700;color:#444;margin-top:12px}
.offer p{font-size:7px;color:var(--muted);margin-top:5px}
.offer .price{color:var(--accent);font-weight:700;font-size:8px;margin-top:5px}

/* info columns */
.col-title{position:absolute;top:908px;font-size:10px;font-weight:400;color:var(--heading);text-transform:uppercase}
.ptype{position:absolute;left:197px;width:250px}
.ptype .num{position:absolute;left:0;top:0;width:31px;height:31px;border-radius:50%;background:var(--accent-soft);color:#fff;font-size:13px;text-align:center;line-height:31px}
.ptype h5{margin-left:47px;font-size:8px;color:#444}
.ptype p{margin-left:47px;font-size:7px;line-height:11px;color:var(--muted);margin-top:5px}
.ptype p a,.col-text a{color:var(--accent)}
.photo{position:absolute;top:936px;width:176px;height:111px;background:#fff;padding:3px;box-shadow:0 0 2px rgba(0,0,0,.2)}
.photo div{width:100%;height:100%}
.col-text{position:absolute;top:1059px;width:180px;font-size:7px;line-height:11px;color:var(--muted)}

/* footer */
.site-footer{position:absolute;left:0;top:1115px;width:1200px;height:77px;background:var(--ink)}
.foot-nav{position:absolute;left:197px;top:37px;font-size:7px;color:#ccc}
.foot-nav span{margin:0 4px;color:#666}
.social{position:absolute;left:197px;top:56px;display:flex;gap:3px}
.social i{width:9px;height:9px;background:#ccc;display:block}
</style>
</head>
<body>

<header class="site-header">
  <div class="brand"><span class="brand-dot"></span><span class="brand-name">Meridale Real Estate</span></div>
  <div class="follow">Follow us on <b>Chirpline, Friendsbook</b></div>
  <div class="search-box"><svg width="9" height="9" viewBox="0 0 9 9"><circle cx="3.5" cy="3.5" r="2.5" fill="none" stroke="#ccc" stroke-width="1.2"/><line x1="5.5" y1="5.5" x2="8" y2="8" stroke="#ccc" stroke-width="1.2"/></svg></div>
  <nav class="main-nav">
    <a class="active" href="#" style="left:113px">Home</a>
    <a href="#" style="left:216px">About Us</a>
    <a href="#" style="left:319px">Buying</a>
    <a href="#" style="left:411px">Selling</a>
    <a href="#" style="left:500px">Leasing</a>
    <a href="#" style="left:589px">Contact Us</a>
  </nav>
</header>

<section class="hero" role="img" aria-label="Photo of a white two-storey house with a red tiled roof and a white patio umbrella"></section>
<aside class="listing">
  <h2 class="listing-title">418 Larkmont Avenue,<br>CA 9000</h2>
  <dl>
    <dt>MLS#</dt><dd>18700</dd>
    <dt>Status</dt><dd>ACTIVE</dd>
    <dt>Price</dt><dd>$1,333,567</dd>
    <dt>Bed</dt><dd>5/3</dd>
    <dt>Lot Size</dt><dd>2.2 Acre</dd>
    <dt>Bed</dt><dd>2-Car Garage Attached</dd>
    <dt>Garage</dt><dd>5/3</dd>
    <dt>Taxes</dt><dd>$18,567</dd>
  </dl>
  <a class="more" href="#">MORE INFO &gt;&gt;</a>
</aside>

<div class="band"></div>
<section class="finder">
  <h3 class="panel-title finder-title">Find Your Property</h3>
  <label class="field" style="left:18px;top:52px"><span>Budget</span><i></i></label>
  <label class="field" style="left:122px;top:52px"><span>Type</span><i class="sel"></i></label>
  <label class="field" style="left:226px;top:52px"><span>Location</span><i class="sel"></i></label>
  <label class="field" style="left:18px;top:90px"><span>Square Ft</span><i class="sel"></i></label>
  <label class="field" style="left:122px;top:90px"><span>Min bedrooms</span><i class="sel"></i></label>
  <label class="field" style="left:226px;top:90px"><span>Time Frame</span><i class="sel"></i></label>
  <a class="btn-search" href="#">Search</a>
  <div class="hint">Know exactly what you want? Try our <a href="#">Advanced search</a></div>
  <div class="divider"></div>
  <div class="welcome">
    <h3 class="panel-title">Welcome to our website !</h3>
    <div class="welcome-lead">Our services are tailored to our clients with the following in mind.</div>
    <p class="welcome-text">Lorem ipsum dolor sit amet, consectetur adipiscing elit, sed do eiusmod tempor incid-<br>dunt ut labore et dolore magna aliqua.</p>
    <a class="btn-alert" href="#">Property Alerts</a>
  </div>
</section>

<h2 class="section-title">Featured Offers</h2>
<article class="offer" style="left:197px"><div class="thumb"><div role="img" aria-label="Photo of a modern office building" style="background:linear-gradient(180deg,#5b9bd8,#c9d6e2 60%,#8d8f92)"></div><span class="date">10<small>June</small></span></div><h4>Office Building &gt;&gt;</h4><p>Lorem ipsum dolor sit amet</p><div class="price">$1234.00</div></article>
<article class="offer" style="left:352px"><div class="thumb"><div role="img" aria-label="Photo of a traditional brick family home" style="background:linear-gradient(180deg,#c8d6e4,#8a6a58 55%,#5d6d45)"></div><span class="date">12<small>June</small></span></div><h4>Traditional Home &gt;&gt;</h4><p>Lorem ipsum dolor sit amet</p><div class="price">$1234.00</div></article>
<article class="offer" style="left:509px"><div class="thumb"><div role="img" aria-label="Photo of a farm ranch with green fields" style="background:linear-gradient(180deg,#cfe0ea,#6f9a3e 45%,#8a6a3a)"></div><span class="date">12<small>June</small></span></div><h4>Farm Ranch &gt;&gt;</h4><p>Lorem ipsum dolor sit amet</p><div class="price">$1234.00</div></article>
<article class="offer" style="left:664px"><div class="thumb"><div role="img" aria-label="Photo of a bright living room interior" style="background:linear-gradient(180deg,#8a7a6a,#d9d2c8 55%,#b8aa98)"></div><span class="date">12<small>June</small></span></div><h4>Home Interior &gt;&gt;</h4><p>Lorem ipsum dolor sit amet</p><div class="price">$1234.00</div></article>
<article class="offer" style="left:821px"><div class="thumb"><div role="img" aria-label="Photo of a country home at dusk with a pool" style="background:linear-gradient(180deg,#3a5fa8,#7d8fbf 50%,#d9c49a 75%,#2f3f6a)"></div><span class="date">12<small>June</small></span></div><h4>Country Home &gt;&gt;</h4><p>Lorem ipsum dolor sit amet</p><div class="price">$1234.00</div></article>

<h3 class="col-title" style="left:197px">Property Type</h3>
<div class="ptype" style="top:936px"><span class="num">01</span><h5>Commercial</h5><p>Lorem ipsum dolor sit amet, consectetur adipiscing elit, sed do et dolore magna aliqua aliquip ex ea commodo consequat <a href="#">[....]</a></p></div>
<div class="ptype" style="top:986px"><span class="num">02</span><h5>Residential</h5><p>Lorem ipsum dolor sit amet, consectetur a aliquip ex ea commodo consequat <a href="#">[....]</a></p></div>
<div class="ptype" style="top:1034px"><span class="num">03</span><h5>Farm Ranch</h5><p>Lorem ipsum dolor sit amet, consectetur adipiscing elit, sed do labore et dolore magna aliqua aliquip ex ea commodo consequat <a href="#">[....]</a></p></div>

<h3 class="col-title" style="left:524px">Buyer</h3>
<div class="photo" style="left:527px"><div role="img" aria-label="Photo of house keys being handed over in front of a lawn" style="background:linear-gradient(180deg,#2e3a3a,#5f7a4a 55%,#4e9a3a)"></div></div>
<p class="col-text" style="left:524px">Lorem ipsum dolor sit amet, consectetur adipiscing elit, sed labore et dolore magna aliqua aliquip ex ea com-modo consequat <a href="#">[....]</a></p>

<h3 class="col-title" style="left:781px">Seller Representation</h3>
<div class="photo" style="left:784px"><div role="img" aria-label="Photo of a hand holding house keys in front of a home" style="background:linear-gradient(180deg,#c9b9a6,#a88f72 50%,#5e6f4a)"></div></div>
<p class="col-text" style="left:781px">Lorem ipsum dolor sit amet, consectetur adipiscing elit, sed labore et dolore magna aliqua aliquip ex ea com-modo consequat <a href="#">[....]</a></p>

<footer class="site-footer">
  <nav class="foot-nav"><a href="#">HOME</a><span>|</span><a href="#">ABOUT US</a><span>|</span><a href="#">BUYING</a><span>|</span><a href="#">SELLING</a><span>|</span><a href="#">LEASING</a><span>|</span><a href="#">CONTACTS</a></nav>
  <div class="social"><i></i><i></i><i></i><i></i></div>
</footer>

</body>
</html>
```